Velkora Land Surveying Website Design

We are working with Velkora. They are a national land surveying company and in need of a new website design.

Some sites to use for inspiration:

https://brannickeng.com
https://www.dvwinc.com
https://kelvarin.com
https://gto.us
https://ravendobuilt.com
https://www.marbeckquillondale.com

Thank you for taking the time to consider designing a website for us. We are web developers based in Stockton and Los Angeles, CA, USA. Most of our projects go through the same process. Understanding this process may help you win a project with us. We custom-code all of our websites in-house. We don’t have any requirements as to what tools you use for your design, but we prefer Figma files. For any design that we label as four-stars, we send it to the client for review. The client picks the final design they want us to use. Once we complete this process, we will continue to show additional clients all the four-star sites and purchase them later. Your designs will have multiple chances to sell. For better chances of success, we ask that you follow these guidelines.

IMAGES:
If you use any images or icons in the design, we ask that you have a link to the asset so we can purchase the image/icon. Most of the designs we submit do not have the customer’s images on them unless they have some great images. Be creative; show us the feeling you are trying to portray with your image choices. Use any royalty-free site you choose. We subscribe to Pellix and mainly use their images, but we can purchase images outside of Pellix.

PLEASE NOTE: we will not submit designs to clients with watermarks on the images.

FONTS:
We ask that you identify the fonts used in the design. This can be done in a message if you want. We typically use Google Fonts and Pellix Fonts.

CONTENT:
We're always open to different content and ideas. We often submit designs with stock images so the client can see our vision. We typically take pictures after the website launch to use their images with our vision. Lorem Ipsum is fine for paragraphs, but we ask that you write the headers in correct English. We want to be able to show the vision and identify the sections of the website.

INSPIRATION:
We typically add a couple of links in the brief of websites we like to help you get started in your design.

REVISIONS:
We do not often ask for revisions of the designs unless we see something in the design that may not appeal to the client. If there are slight changes that we want to make, we do that in the development process.

FEEDBACK:
We rarely give feedback on designs during the design process. We are working on many website projects and do not have the time to provide feedback. We usually respond if your request is well thought out and asks specific questions, but a note asking “feedback, please” usually goes unanswered.

```html
<!DOCTYPE html>
<html lang="en">
<head>
<meta charset="utf-8">
<title>Velkora Land Surveying</title>
<link rel="stylesheet" href="https://fonts.googleapis.com/css2?family=Montserrat:wght@300;400;500;600;700;800&display=swap">
<style>
:root{
  --red:#e0453a;
  --red-soft:#e15b50;
  --gray:#7a7a7a;
  --gray-dark:#6f6f6f;
  --ink:#222;
  --text:#555;
  --white:#fff;
  --pink:#f6c9c4;
}
*{margin:0;padding:0;box-sizing:border-box}
html,body{width:1200px;height:3688px;overflow:hidden}
body{position:relative;background:var(--white);font-family:'Montserrat',sans-serif;color:var(--ink)}
a{color:inherit;text-decoration:none}
.abs{position:absolute}
.arrow{display:inline-block;width:16px;height:10px;margin-left:8px;vertical-align:middle;flex:none}
.btn{position:absolute;display:flex;align-items:center;justify-content:center;background:var(--red);color:var(--white);font-size:16px;font-weight:500;white-space:nowrap}
.btn.inline{position:static;align-self:flex-start;padding:0 14px}

/* header */
.site-header{position:absolute;left:0;top:0;width:1200px;height:86px;background:var(--white);z-index:5}
.brand{position:absolute;left:112px;top:24px;display:flex;align-items:center;gap:12px;color:var(--red);font-weight:700;font-size:22px}
.brand-dot{width:36px;height:36px;border-radius:50%;background:var(--red)}
.main-nav a{position:absolute;top:32px;font-size:16px;color:#333}
.main-nav a.active{color:var(--red);border-bottom:2px solid var(--red);padding-bottom:2px}
.search{position:absolute;left:1074px;top:34px}

/* hero */
.hero{position:absolute;left:0;top:86px;width:1200px;height:600px}
.hero > svg{position:absolute;left:0;top:0}
.hero-title{position:absolute;left:112px;top:104px;color:var(--white);font-size:45px;line-height:58px;font-weight:800}
.hero-title span{font-weight:500;display:block}
.hero-text{position:absolute;left:112px;top:234px;width:480px;color:var(--white);font-size:18px;line-height:28px}

/* section heading */
.heading{font-size:40px;line-height:46px;font-weight:700;color:var(--red);text-transform:uppercase}
.heading .light{color:var(--gray);font-weight:400}

/* about */
.about-body{position:absolute;left:112px;top:916px;width:640px;display:flex;flex-direction:column;gap:14px}
.about-text{font-size:16.5px;line-height:25.5px;color:var(--text)}
.vline{position:absolute;width:2px;background:#333}
.stat{position:absolute;left:828px;width:260px;height:110px;color:var(--white);padding:16px 22px}
.stat-label{font-size:19px;font-weight:500;padding-bottom:6px;border-bottom:1px solid rgba(255,255,255,.5)}
.stat-value{font-size:37px;font-weight:300;margin-top:8px}

/* services */
.services{position:absolute;left:0;top:1183px;width:1200px;height:699px;background:var(--red-soft)}
.services .heading{position:absolute;left:0;top:130px;width:1200px;text-align:center;color:var(--white)}
.services .heading .light{color:var(--white)}
.lead{font-size:17px;line-height:26px;color:var(--text);text-align:center}
.services .lead{position:absolute;left:0;top:201px;width:1200px;color:var(--white)}
.card{position:absolute;top:278px;width:311px;height:272px;border:2px solid var(--white);color:var(--white);padding:26px 33px}
.card.solid{background:var(--white);color:var(--ink)}
.card-tab{position:absolute;left:-2px;top:36px;width:9px;height:44px;background:var(--white)}
.card.solid .card-tab{background:var(--gray)}
.card-icon{width:64px;height:64px;background:rgba(255,255,255,.9)}
.card.solid .card-icon{background:var(--red)}
.card h3{margin-top:22px;font-size:19px;font-weight:500}
.card p{margin-top:16px;font-size:14px;line-height:21px}
.card.solid p{color:var(--text)}
.card .more{display:block;margin-top:8px;font-size:15px;text-decoration:underline}
.card.solid .more{color:var(--red)}
.btn-light{background:var(--white);color:var(--red)}

/* featured */
.featured-body{position:absolute;left:577px;top:1981px;width:520px;display:flex;flex-direction:column;gap:14px}
.featured-text{font-size:16.5px;line-height:25.5px;color:var(--text)}
.slide-side{position:absolute;opacity:.35}
.slide-label{position:absolute;background:var(--pink);color:var(--white);font-size:19px;font-weight:600;padding:12px 18px;overflow:hidden;white-space:nowrap}
.slide-label small{display:block;font-size:13px;font-weight:400;margin-top:6px}
.caption{position:absolute;left:319px;top:2522px;width:560px;height:69px;background:var(--red);color:var(--white);text-align:center;padding-top:10px}
.caption h4{font-size:19px;font-weight:600}
.caption p{font-size:13.5px;margin-top:8px}
.caption p i{display:inline-block;width:1px;height:16px;background:var(--white);margin:0 10px;vertical-align:middle}

/* news */
.news-card{position:absolute;top:2880px;width:311px}
.news-img{width:311px;height:209px}
.news-meta{display:flex;justify-content:space-between;margin-top:25px;font-size:13.5px;color:var(--text)}
.news-meta .cat{color:var(--red)}
.news-card h3{margin-top:12px;font-size:16px;line-height:25px;font-weight:600;color:#111}
.news-card p{margin-top:6px;font-size:13px;line-height:20px;color:var(--text)}
.news-card .more{display:inline-block;margin-top:14px;font-size:15px;color:var(--red);text-decoration:underline}

/* footer */
.site-footer{position:absolute;left:0;top:3290px;width:1200px;height:398px;color:var(--white)}
.site-footer > svg{position:absolute;left:0;top:0}
.footer-brand{position:absolute;left:0;top:222px;width:1200px;display:flex;justify-content:center;align-items:center;gap:16px;font-size:40px;font-weight:700}
.footer-brand .brand-dot{width:56px;height:56px;background:var(--white)}
.footer-nav a{position:absolute;top:301px;font-size:18px}
.footer-rule{position:absolute;left:112px;top:342px;width:976px;height:1px;background:rgba(255,255,255,.6)}
.copy{position:absolute;left:112px;top:358px;font-size:13px}
.legal{position:absolute;right:112px;top:358px;font-size:13px}
</style>
</head>
<body>

<header class="site-header">
  <a class="brand" href="#"><span class="brand-dot"></span>Velkora Land Surveying</a>
  <nav class="main-nav">
    <a class="active" href="#" style="left:489px">Home</a>
    <a href="#" style="left:581px">About</a>
    <a href="#" style="left:673px">Services</a>
    <a href="#" style="left:781px">Projects</a>
    <a href="#" style="left:887px">Blog</a>
    <a href="#" style="left:968px">Contact</a>
  </nav>
  <svg class="search" width="16" height="16" viewBox="0 0 16 16"><circle cx="6.5" cy="6.5" r="5" fill="none" stroke="#222" stroke-width="2"/><line x1="10.2" y1="10.2" x2="15" y2="15" stroke="#222" stroke-width="2.4"/></svg>
</header>

<section class="hero">
  <svg width="1200" height="600" viewBox="0 0 1200 600" role="img" aria-label="Surveyor in hard hat and orange vest looking through a level on a tripod">
    <defs>
      <linearGradient id="heroFill" x1="0" y1="0" x2="1" y2="0">
        <stop offset="0" stop-color="#1d1d19"/>
        <stop offset=".45" stop-color="#3b3a30"/>
        <stop offset=".75" stop-color="#8a7a62"/>
        <stop offset="1" stop-color="#c9a47a"/>
      </linearGradient>
    </defs>
    <path d="M0 0H1200V447Q600 630 0 447Z" fill="url(#heroFill)"/>
    <path d="M143 501Q594 666 1045 501Q594 623 143 501Z" fill="var(--red)"/>
  </svg>
  <h1 class="hero-title">PRECISION SURVEYING.<span>NATIONWIDE REACH.</span></h1>
  <p class="hero-text">From boundary to infrastructure, we deliver accurate geospatial solutions.</p>
  <a class="btn" href="#" style="left:112px;top:321px;width:174px;height:38px">Request a Quote<svg class="arrow" viewBox="0 0 16 10"><path d="M0 5H14M10 1L14 5L10 9" stroke="#fff" stroke-width="2" fill="none"/></svg></a>
</section>

<section class="about">
  <h2 class="heading abs" style="left:112px;top:806px">About Velkora<br><span class="light">Land Surveying</span></h2>
  <div class="about-body">
    <p class="about-text">Lorem ipsum dolor sit amet, consectetur adipiscing elit, sed do eiusmod tempor incididunt ut labore et dolore magna aliqua. Ut enim ad minim veniam, quis nostrud exercitation ullamco laboris nisi ut aliquip ex ea commodo consequat. Duis aute irure dolor in reprehenderit in voluptate velit esse cillum dolore eu fugiat nulla pariatur.</p>
    <a class="btn inline" href="#" style="height:37px">More About Us<svg class="arrow" viewBox="0 0 16 10"><path d="M0 5H14M10 1L14 5L10 9" stroke="#fff" stroke-width="2" fill="none"/></svg></a>
  </div>
  <div class="vline" style="left:795px;top:859px;height:238px"></div>
  <div class="stat" style="top:868px;background:var(--red)"><div class="stat-label">YEAR FOUNDED</div><div class="stat-value">1978</div></div>
  <div class="stat" style="top:986px;background:var(--gray)"><div class="stat-label">PROJECTS</div><div class="stat-value">90,000+</div></div>
</section>

<section class="services">
  <h2 class="heading">Our <span class="light">Services</span></h2>
  <p class="lead">Lorem ipsum dolor sit amet, consectetur adipiscing elit, sed do eiusmod tempor incididunt<br>ut labore et dolore magna aliqua. Ut enim ad minim veniam, quis nostrud exercitation ullamco laboris nisi</p>
  <article class="card" style="left:112px">
    <span class="card-tab"></span>
    <div class="card-icon" role="img" aria-label="Drone survey icon"></div>
    <h3>Boundary Surveys</h3>
    <p>Accurate property line determination for landowners, developers, and municipalities.</p>
    <a class="more" href="#">Learn More</a>
  </article>
  <article class="card solid" style="left:446px">
    <span class="card-tab"></span>
    <div class="card-icon" role="img" aria-label="Surveyor at tripod icon"></div>
    <h3>Topographic Surveys</h3>
    <p>Detailed mapping of natural and man-made features for design and planning.</p>
    <a class="more" href="#">Learn More</a>
  </article>
  <article class="card" style="left:778px">
    <span class="card-tab"></span>
    <div class="card-icon" role="img" aria-label="Site layout plan icon"></div>
    <h3>Construction Layout</h3>
    <p>Precision staking and layout services to guide construction from start to finish.</p>
    <a class="more" href="#">Learn More</a>
  </article>
  <a class="btn btn-light" href="#" style="left:530px;top:576px;width:143px;height:37px">View More<svg class="arrow" viewBox="0 0 16 10"><path d="M0 5H14M10 1L14 5L10 9" stroke="#e0453a" stroke-width="2" fill="none"/></svg></a>
</section>

<section class="featured">
  <h2 class="heading abs" style="left:112px;top:2014px">Featured<br><span class="light">Project</span></h2>
  <div class="vline" style="left:544px;top:1973px;height:152px"></div>
  <div class="featured-body">
    <p class="featured-text">Lorem ipsum dolor sit amet, consectetur adipiscing elit, sed do eiusmod tempor incididunt ut labore et dolore magna aliqua. Ut enim ad minim veniam, quis nostrud exercitation</p>
    <a class="btn inline" href="#" style="height:37px">View More<svg class="arrow" viewBox="0 0 16 10"><path d="M0 5H14M10 1L14 5L10 9" stroke="#fff" stroke-width="2" fill="none"/></svg></a>
  </div>

  <div class="slide-side" style="left:0;top:2164px;width:190px;height:321px;background:linear-gradient(135deg,#5d7a3c,#9aa877)" role="img" aria-label="Aerial view of a residential development"></div>
  <div class="slide-label" style="left:0;top:2465px;width:159px;height:68px">lopment<small>nic Survey</small></div>
  <div class="slide-side" style="left:1012px;top:2164px;width:188px;height:321px;background:linear-gradient(135deg,#b8bcc0,#e4e2dc)" role="img" aria-label="Construction site with building frame"></div>
  <div class="slide-label" style="left:1043px;top:2465px;width:157px;height:68px">Highlanc<small>Denver</small></div>

  <div class="abs" style="left:289px;top:2221px;width:622px;height:321px;background:linear-gradient(135deg,#2f5a26,#4f7d33 55%,#98ad4a)" role="img" aria-label="Aerial view of farmland and development parcels"></div>
  <div class="caption">
    <h4>Highland Ridge Commercial Development</h4>
    <p><svg width="10" height="13" viewBox="0 0 10 13" style="vertical-align:-1px;margin-right:5px"><path d="M5 0A5 5 0 0 1 10 5C10 8 5 13 5 13S0 8 0 5A5 5 0 0 1 5 0Z" fill="#fff"/></svg>Denver, CO<i></i>Boundary Survey, Topographic Survey</p>
  </div>
  <svg class="abs" style="left:248px;top:2347px" width="68" height="68" viewBox="0 0 68 68"><circle cx="34" cy="34" r="33" fill="#fff"/><circle cx="34" cy="34" r="26" fill="var(--gray-dark)"/><path d="M44 34H25M32 26L24 34L32 42" stroke="#fff" stroke-width="3" fill="none"/></svg>
  <svg class="abs" style="left:881px;top:2347px" width="68" height="68" viewBox="0 0 68 68"><circle cx="34" cy="34" r="33" fill="#fff"/><circle cx="34" cy="34" r="26" fill="var(--red)"/><path d="M24 34H43M36 26L44 34L36 42" stroke="#fff" stroke-width="3" fill="none"/></svg>
</section>

<section class="news">
  <h2 class="heading abs" style="left:0;top:2722px;width:1200px;text-align:center">Latest <span class="light">News &amp; Insight</span></h2>
  <p class="lead abs" style="left:0;top:2792px;width:1200px">Lorem ipsum dolor sit amet, consectetur adipiscing elit, sed do eiusmod tempor incididunt<br>ut labore et dolore magna aliqua. Ut enim ad minim veniam, quis nostrud exercitation ullamco laboris nisi</p>
  <article class="news-card" style="left:112px">
    <div class="news-img" style="background:linear-gradient(180deg,#7c8590,#4a4a46)" role="img" aria-label="Surveyor placing a marker stake in gravel"></div>
    <div class="news-meta"><span class="cat">Lorem Ipsum</span><span>22 Aug 2025</span></div>
    <h3>Lorem ipsum dolor sit amet, consec tetur adipiscing elit, sed do...</h3>
    <p>Lorem ipsum dolor sit amet, consectetur adi piscing elit, sed do eiusmod tempor</p>
    <a class="more" href="#">Learn More</a>
  </article>
  <article class="news-card" style="left:445px">
    <div class="news-img" style="background:linear-gradient(180deg,#6e6a63,#b49a78)" role="img" aria-label="Surveyor kneeling beside a tripod on a dirt site"></div>
    <div class="news-meta"><span class="cat">Lorem Ipsum</span><span>22 Aug 2025</span></div>
    <h3>Lorem ipsum dolor sit amet, consec tetur adipiscing elit, sed do...</h3>
    <p>Lorem ipsum dolor sit amet, consectetur adi piscing elit, sed do eiusmod tempor</p>
    <a class="more" href="#">Learn More</a>
  </article>
  <article class="news-card" style="left:778px">
    <div class="news-img" style="background:linear-gradient(180deg,#c8d8e4,#b89a5c)" role="img" aria-label="Surveyor with total station in a wheat field"></div>
    <div class="news-meta"><span class="cat">Lorem Ipsum</span><span>22 Aug 2025</span></div>
    <h3>Lorem ipsum dolor sit amet, consec tetur adipiscing elit, sed do...</h3>
    <p>Lorem ipsum dolor sit amet, consectetur adi piscing elit, sed do eiusmod tempor</p>
    <a class="more" href="#">Learn More</a>
  </article>
</section>

<footer class="site-footer">
  <svg width="1200" height="398" viewBox="0 0 1200 398">
    <path d="M0 204Q600 10 1200 204V398H0Z" fill="var(--gray-dark)"/>
    <path d="M158 137Q600 -25 1045 137Q600 30 158 137Z" fill="var(--red)"/>
  </svg>
  <div class="footer-brand"><span class="brand-dot"></span>Velkora Land Surveying</div>
  <nav class="footer-nav">
    <a href="#" style="left:299px">Home</a>
    <a href="#" style="left:401px">About</a>
    <a href="#" style="left:504px">Services</a>
    <a href="#" style="left:624px">Projects</a>
    <a href="#" style="left:742px">Blog</a>
    <a href="#" style="left:832px">Contact</a>
  </nav>
  <div class="footer-rule"></div>
  <p class="copy">Copyright © 2025 Velkora Land Surveying. All rights reserved.</p>
  <p class="legal">Privacy Policy &nbsp;|&nbsp; Terms &amp; Conditions &nbsp;|&nbsp; Cookies Policy</p>
</footer>

</body>
</html>
```